Emerging Ed-Tech Startup seeking Stationery Designs!

We are in need of basic set of stationery designs to be used for our business operations, letters, emails, and in-office materials. We are a technology startup enhancing on campus work experience offerings by establishing a collaborative work environment for the completion of such tasks.

Our colors are Vibrant Tiffany Blue/Black/White.

Website: www.campusnorthway.com (Still under construction aside from the landing pages)

Please make sure the designs use a brighter more vibrant tiffany blue color than seen in the image files uploaded. We are not using those materials.

Our logo has been added as a file as well, please use that for any designs (include that logo). Thank you.

```html
<!DOCTYPE html>
<html lang="en">
<head>
<meta charset="utf-8">
<title>Campus Northway Stationery Set</title>
<link rel="stylesheet" href="https://fonts.googleapis.com/css2?family=Jost:wght@400;500;700&family=Arimo:wght@400&display=swap">
<style>
  :root {
    --tiffany: #0fe6e6;
    --ink: #111111;
    --paper: #ffffff;
    --backdrop: #9a7550;
    --rule: #444444;
    --faint: #e9eef0;
    --text: #222222;
  }
  * { box-sizing: border-box; margin: 0; padding: 0; }
  html, body { width: 1200px; height: 700px; overflow: hidden; }
  body {
    position: relative;
    background: var(--backdrop);
    font-family: "Jost", sans-serif;
    color: var(--text);
  }
  .sheet {
    position: absolute;
    background: var(--paper);
    border: 1px solid #5a4630;
    overflow: hidden;
  }
  .wordmark {
    position: absolute;
    display: flex;
    align-items: center;
    gap: 4px;
  }
  .wordmark__square {
    width: 10px; height: 10px;
    background: var(--tiffany);
  }
  .wordmark__name {
    font-family: "Jost", sans-serif;
    font-weight: 700;
    font-size: 14px;
    line-height: 14px;
    color: var(--ink);
    text-transform: uppercase;
  }
  .wave { position: absolute; left: 0; bottom: 0; width: 100%; display: block; }
  .contact-list {
    position: absolute;
    font-size: 6px;
    line-height: 10px;
    color: var(--text);
    list-style: none;
  }
  .contact-list--ruled { border-left: 1px solid var(--rule); padding-left: 5px; }
  .footer-line {
    position: absolute;
    left: 0; width: 100%;
    text-align: center;
    font-size: 6px;
    letter-spacing: 0.3px;
    color: var(--text);
  }

  /* Letterhead */
  .letterhead { left: 70px; top: 45px; width: 327px; height: 422px; }
  .letterhead .wordmark { left: 14px; top: 14px; }
  .letterhead .contact-list { left: 235px; top: 18px; }
  .letterhead__watermark {
    position: absolute; left: 92px; top: 155px;
    width: 140px; height: 135px;
    background: var(--faint);
  }
  .letterhead .footer-line { bottom: 7px; }

  /* Fax */
  .fax { left: 432px; top: 45px; width: 327px; height: 422px; }
  .fax .wordmark { left: 120px; top: 14px; }
  .fax .contact-list { left: 238px; top: 29px; }
  .fax__title {
    position: absolute; left: 25px; top: 89px;
    font-family: "Arimo", sans-serif; font-size: 20px; color: var(--ink);
  }
  .fax__fields { position: absolute; left: 27px; top: 130px; width: 272px; }
  .fax__row {
    display: grid; grid-template-columns: 176px 1fr;
    height: 38.5px; padding-top: 3px;
    border-bottom: 1px solid var(--rule);
    font-family: "Arimo", sans-serif; font-size: 8px; color: var(--text);
    margin-bottom: 0;
  }
  .fax .footer-line { bottom: 6px; }

  /* Right panels */
  .panel { left: 779px; width: 366px; height: 158px; }
  .panel--plain { top: 43px; }
  .panel--black { top: 220px; }
  .panel--tiffany { top: 393px; }
  .panel__band {
    position: absolute; left: 0; top: 0; width: 100%; height: 56px;
    display: flex; align-items: center; justify-content: center;
  }
  .panel--plain .panel__band { border-bottom: 1px solid var(--rule); }
  .panel--black .panel__band { background: var(--ink); }
  .panel--tiffany .panel__band { background: var(--tiffany); }
  .panel__band .wordmark { position: static; }
  .panel--black .wordmark__name { color: var(--paper); }
  .panel--tiffany .wordmark__name { color: var(--paper); }
  .panel--tiffany .wordmark__square { background: var(--paper); }

  /* Email signature */
  .signature { left: 65px; top: 505px; width: 347px; height: 95px; }
  .signature .wordmark { left: 14px; top: 9px; }
  .signature__address {
    position: absolute; right: 10px; top: 10px;
    text-align: right; font-size: 6.5px; line-height: 9px; font-weight: 500;
  }
  .signature__contacts {
    position: absolute; left: 14px; top: 78px; font-size: 6px;
  }
  .signature__person {
    position: absolute; right: 14px; top: 64px;
    text-align: right; font-size: 7.5px; line-height: 12px;
    font-weight: 500; text-transform: uppercase; color: var(--ink);
  }
  .caption {
    position: absolute; left: 170px; top: 622px;
    font-size: 16px; color: var(--paper);
  }

  /* Envelope */
  .envelope { left: 469px; top: 491px; width: 365px; height: 158px; }
  .envelope .wordmark { left: 15px; top: 14px; }
  .envelope__address { position: absolute; left: 15px; top: 66px; font-size: 5.5px; }
  .envelope .footer-line { bottom: 8px; }
  .envelope__mark {
    position: absolute; right: 17px; bottom: 8px;
    width: 30px; height: 28px; background: #7ff2f2;
  }
</style>
</head>
<body>

  <!-- Letterhead -->
  <section class="sheet letterhead">
    <div class="wordmark"><span class="wordmark__square"></span><span class="wordmark__name">Campus<br>Northway</span></div>
    <ul class="contact-list contact-list--ruled">
      <li>&#9742; +91 40 5528170</li>
      <li>&#9743; +91 40 5528171</li>
      <li>&#9679; www.campusnorthway.com</li>
    </ul>
    <div class="letterhead__watermark"></div>
    <svg class="wave" viewBox="0 0 327 56" preserveAspectRatio="none" aria-hidden="true">
      <path d="M0,12 C110,34 230,-6 327,6 L327,56 L0,56 Z" fill="var(--tiffany)"/>
      <path d="M0,10 C110,32 230,-8 327,2 C230,-2 110,38 0,15 Z" fill="var(--ink)"/>
    </svg>
    <p class="footer-line">Suite#B-14 Lake Road</p>
  </section>

  <!-- Fax sheet -->
  <section class="sheet fax">
    <div class="wordmark"><span class="wordmark__square"></span><span class="wordmark__name">Campus<br>Northway</span></div>
    <ul class="contact-list contact-list--ruled"><li>Suite#B-14 Lake Road</li></ul>
    <h1 class="fax__title">FAX</h1>
    <div class="fax__fields">
      <div class="fax__row"><span>To</span><span>From</span></div>
      <div class="fax__row"><span>Fax</span><span>Pages</span></div>
      <div class="fax__row"><span>Phone</span><span>Date</span></div>
      <div class="fax__row"><span>Re</span><span>CC</span></div>
    </div>
    <svg class="wave" viewBox="0 0 327 56" preserveAspectRatio="none" aria-hidden="true">
      <path d="M0,12 C110,34 230,-6 327,6 L327,56 L0,56 Z" fill="var(--tiffany)"/>
      <path d="M0,10 C110,32 230,-8 327,2 C230,-2 110,38 0,15 Z" fill="var(--ink)"/>
    </svg>
    <p class="footer-line">&#9742; +91 40 5528170 &nbsp;&#9743; +91 40 5528171 &nbsp;&#9679; www.campusnorthway.com</p>
  </section>

  <!-- Compliment panels -->
  <section class="sheet panel panel--plain">
    <div class="panel__band"><div class="wordmark"><span class="wordmark__square"></span><span class="wordmark__name">Campus Northway</span></div></div>
  </section>
  <section class="sheet panel panel--black">
    <div class="panel__band"><div class="wordmark"><span class="wordmark__square"></span><span class="wordmark__name">Campus Northway</span></div></div>
  </section>
  <section class="sheet panel panel--tiffany">
    <div class="panel__band"><div class="wordmark"><span class="wordmark__square"></span><span class="wordmark__name">Campus Northway</span></div></div>
  </section>

  <!-- Email signature -->
  <section class="sheet signature">
    <div class="wordmark"><span class="wordmark__square"></span><span class="wordmark__name">Campus<br>Northway</span></div>
    <p class="signature__address">&#8962; Suite#B-14<br>Lake Road</p>
    <svg class="wave" viewBox="0 0 347 50" preserveAspectRatio="none" aria-hidden="true">
      <path d="M0,10 C120,30 240,-4 347,4 L347,50 L0,50 Z" fill="var(--tiffany)"/>
      <path d="M0,8 C120,28 240,-6 347,0 C240,-1 120,34 0,13 Z" fill="var(--ink)"/>
    </svg>
    <p class="signature__contacts">&#9742; +91 40 5528170 &nbsp;&#9743; +91 40 5528171 &nbsp;&#9679; www.campusnorthway.com</p>
    <p class="signature__person">Mr. Neil Carver<br>Marketing Manager</p>
  </section>
  <p class="caption">Email Signtaure</p>

  <!-- Envelope -->
  <section class="sheet envelope">
    <div class="wordmark"><span class="wordmark__square"></span><span class="wordmark__name">Campus<br>Northway</span></div>
    <p class="envelope__address">Suite#B-14 Lake Road</p>
    <svg class="wave" viewBox="0 0 365 48" preserveAspectRatio="none" aria-hidden="true">
      <path d="M0,10 C120,32 250,-4 365,4 L365,48 L0,48 Z" fill="var(--tiffany)"/>
      <path d="M0,8 C120,30 250,-6 365,0 C250,-1 120,36 0,13 Z" fill="var(--ink)"/>
    </svg>
    <p class="footer-line">www.campusnorthway.com</p>
    <div class="envelope__mark"></div>
  </section>

</body>
</html>
```